Hollow Marigold Distillery

I need a label designed for my small distillery. I’d like it to have a rose, and the name hollow marigold in script writing. I need the graphic to fit a standard gin bottle and I’ll need to be able to edit it depending on alcohol, warning and descriptions. I want it to look elegant and attractive, but slightly daring too. It’s a 700ml oslo bottle
Target Market(s)
Bespoke gin and vodka drinkers
Industry/Entity Type
Beverage
Font styles to use
Script
Other font styles liked:
- Something easy to read
Requirements
Must have
- Room for me to add and remove text depending on the drink
Nice to have
- Hollow marigold in script, slight colour on the rose and black writing

```html
<!DOCTYPE html>
<html lang="en">
<head>
<meta charset="utf-8">
<title>Hollow Marigold Distillery – Vodka Label Variations</title>
<link href="https://fonts.googleapis.com/css2?family=Pinyon+Script&family=Kaushan+Script&family=Libre+Caslon+Text&family=Oswald:wght@500&display=swap" rel="stylesheet">
<style>
  :root {
    --page: #ffffff;
    --label: #eeeef1;
    --label-edge: #d9d9de;
    --ink: #161616;
    --navy: #24237a;
    --navy-soft: #5a5a9c;
    --rose-light: #e3e3f0;
    --rose-mid: #c9c9e2;
  }
  * { box-sizing: border-box; margin: 0; padding: 0; }
  html, body { width: 1200px; height: 1200px; overflow: hidden; background: var(--page); }
  .canvas { position: relative; width: 1200px; height: 1200px; }

  .variant { position: absolute; top: 0; width: 420px; height: 1200px; }
  .variant--classic { left: 90px; }
  .variant--framed { left: 690px; }

  .neck-strip { position: absolute; top: 90px; left: 184px; width: 52px; height: 240px; }

  .label { position: absolute; top: 400px; left: 0; width: 420px; height: 580px; }
  .label-shape { position: absolute; inset: 0; }

  .brand-name { position: absolute; left: 0; right: 0; text-align: center; line-height: 1; }
  .variant--classic .brand-name { font-family: "Pinyon Script", cursive; font-size: 80px; color: var(--ink); }
  .variant--classic .brand-name--first { top: 95px; }
  .variant--classic .brand-name--second { top: 180px; }
  .variant--framed .brand-name { font-family: "Kaushan Script", cursive; font-size: 72px; }
  .variant--framed .brand-name--first { top: 98px; color: var(--ink); }
  .variant--framed .brand-name--second { top: 185px; color: var(--navy); }

  .rose-art {
    position: absolute; left: 80px; top: 295px; width: 270px; height: 125px;
    border-radius: 60px;
    background: radial-gradient(ellipse at 60% 50%, var(--rose-mid), var(--rose-light) 70%, transparent 100%);
  }

  .spirit-band {
    position: absolute; display: flex; align-items: center; justify-content: center;
    background: linear-gradient(90deg, var(--navy), var(--navy-soft));
    color: #fff; font-family: "Libre Caslon Text", serif; font-size: 26px; letter-spacing: 1px;
  }
  .variant--classic .spirit-band { left: 0; right: 0; top: 458px; height: 50px; }
  .variant--framed .spirit-band { left: 205px; right: 14px; top: 420px; height: 46px; border-radius: 23px 0 0 23px; }

  .spec-line { position: absolute; font-family: "Oswald", sans-serif; font-weight: 500; font-size: 19px; line-height: 24px; color: var(--ink); text-align: center; }
  .variant--classic .spec-line { left: 0; right: 0; top: 525px; }
  .variant--framed .spec-line { left: 205px; right: 14px; top: 476px; }
</style>
</head>
<body>
<main class="canvas">

  <section class="variant variant--classic">
    <svg class="neck-strip" viewBox="0 0 52 240" aria-hidden="true">
      <rect width="52" height="240" fill="#fff"/>
      <rect x="8" y="4" width="36" height="232" fill="none" stroke="var(--navy)" stroke-width="3"/>
      <text transform="translate(35 222) rotate(-90)" font-family="Pinyon Script, cursive" font-size="30" fill="var(--ink)">Hollow Marigold</text>
    </svg>
    <div class="label">
      <svg class="label-shape" viewBox="0 0 420 580" aria-hidden="true">
        <path d="M0 44 Q0 22 22 20 L210 0 L398 20 Q420 22 420 44 L420 498 Q420 514 404 520 L210 580 L16 520 Q0 514 0 498 Z" fill="var(--label)" stroke="var(--label-edge)"/>
      </svg>
      <div class="brand-name brand-name--first">Hollow</div>
      <div class="brand-name brand-name--second">Marigold</div>
      <div class="rose-art" role="img" aria-label="Navy line illustration of roses with leaves and small blossoms"></div>
      <div class="spirit-band">VODKA</div>
      <div class="spec-line">40% ABV | 700 ML</div>
    </div>
  </section>

  <section class="variant variant--framed">
    <svg class="neck-strip" viewBox="0 0 52 240" aria-hidden="true">
      <rect width="52" height="240" fill="#fff"/>
      <rect x="8" y="4" width="36" height="232" fill="none" stroke="var(--navy)" stroke-width="3"/>
      <text transform="translate(35 222) rotate(-90)" font-family="Pinyon Script, cursive" font-size="30" fill="var(--ink)">Hollow Marigold</text>
    </svg>
    <div class="label">
      <svg class="label-shape" viewBox="0 0 420 580" aria-hidden="true">
        <path d="M0 44 Q0 22 22 20 L210 0 L398 20 Q420 22 420 44 L420 498 Q420 514 404 520 L210 580 L16 520 Q0 514 0 498 Z" fill="var(--label)" stroke="var(--label-edge)"/>
        <path d="M14 50 L210 18 L406 50 L406 506 L210 564 L14 506 Z" fill="none" stroke="var(--navy)" stroke-width="3"/>
      </svg>
      <div class="brand-name brand-name--first">Hollow</div>
      <div class="brand-name brand-name--second">Marigold</div>
      <div class="rose-art" role="img" aria-label="Navy line illustration of roses with leaves and small blossoms"></div>
      <div class="spirit-band">VODKA</div>
      <div class="spec-line">40% ABV | 700 ML</div>
    </div>
  </section>

</main>
</body>
</html>
```